Brightmill Data Works

Our company is about IT hardwares and IT solutions. IT hardware such as PC, RAMS, storage and servers. IT solutions such as project management, BA. We are also selling new technology too.

Target Market(s)

Consumer, Small to Medium Business, Corporate

Requirements
Must have
• The business card must have the following:
• Name:
• Title:
• Contact Number:
• Email address:
• Website:
• Color: Must match the logo color upgrade

```html
<!DOCTYPE html>
<html lang="en">
<head>
<meta charset="utf-8">
<title>Brightmill Data Works – Business Card</title>
<link rel="stylesheet" href="https://fonts.googleapis.com/css2?family=Montserrat:wght@400;500;700;800&display=swap">
<style>
  :root {
    --page: #ececec;
    --card: #2b2a29;
    --card-deep: #232221;
    --ink-light: #f2f2f2;
    --ink-soft: #d9d9d9;
    --accent: #c98a3a;
    --rule: #5a5856;
  }
  * { box-sizing: border-box; margin: 0; padding: 0; }
  html, body { width: 1200px; height: 1141px; overflow: hidden; }
  body {
    background: var(--page);
    font-family: "Montserrat", sans-serif;
    position: relative;
  }
  .card {
    position: absolute;
    left: 250px;
    width: 700px;
    height: 400px;
    background: var(--card);
    box-shadow: 0 6px 18px rgba(0,0,0,0.12);
    overflow: hidden;
  }
  .card-back { top: 130px; }
  .card-front { top: 600px; }

  .back-texture {
    position: absolute; inset: 0;
    background: radial-gradient(ellipse at 60% 50%, #343331 0%, var(--card) 55%, var(--card-deep) 100%);
  }
  .back-content {
    position: absolute; inset: 0;
    display: flex; flex-direction: column; align-items: center; justify-content: center;
    gap: 26px;
  }
  .brand {
    display: flex; align-items: center; gap: 14px;
  }
  .brand-dot {
    width: 26px; height: 26px; border-radius: 50%;
    background: var(--accent);
    flex: none;
  }
  .brand-name {
    color: var(--ink-light);
    font-weight: 800;
    text-transform: uppercase;
    letter-spacing: 1px;
    line-height: 1.05;
  }
  .card-back .brand-name { font-size: 34px; }
  .back-web {
    color: var(--ink-soft);
    font-size: 15px;
    letter-spacing: 0.5px;
  }

  .front-brand {
    position: absolute; left: 50px; top: 0; bottom: 0;
    width: 300px;
    display: flex; align-items: center;
  }
  .card-front .brand-name { font-size: 27px; }
  .divider {
    position: absolute; left: 370px; top: 120px;
    width: 1px; height: 170px;
    background: var(--rule);
  }
  .contact {
    position: absolute; left: 400px; top: 110px;
    color: var(--ink-soft);
    font-size: 14px;
    line-height: 1.55;
  }
  .person-name {
    color: var(--accent);
    font-weight: 800;
    font-size: 20px;
    text-transform: uppercase;
    letter-spacing: 0.5px;
  }
  .person-title { margin-bottom: 6px; font-weight: 500; }
  .address { margin-bottom: 4px; }
  .line { display: flex; align-items: center; gap: 10px; }
  .line svg { width: 14px; height: 14px; flex: none; }
</style>
</head>
<body>

  <section class="card card-back">
    <div class="back-texture" role="img" aria-label="Faint connected-node network pattern across the dark card background"></div>
    <div class="back-content">
      <div class="brand">
        <span class="brand-dot"></span>
        <span class="brand-name">Brightmill Data Works</span>
      </div>
      <p class="back-web">www.brightmilldata.example</p>
    </div>
  </section>

  <section class="card card-front">
    <div class="front-brand">
      <div class="brand">
        <span class="brand-dot"></span>
        <span class="brand-name">Brightmill<br>Data Works</span>
      </div>
    </div>
    <div class="divider"></div>
    <div class="contact">
      <p class="person-name">Daniel Okafor</p>
      <p class="person-title">Managing Director</p>
      <p class="address">Kade Street 118<br>9050 Lindenport</p>
      <p class="line">
        <svg viewBox="0 0 16 16" aria-hidden="true"><path d="M4 1.5 6.2 4.6 4.9 6.3c.8 1.9 2.2 3.4 4.1 4.3l1.6-1.3 3 2.2-1 2.6C7.5 14 2 8.6 1.6 3.3Z" fill="var(--accent)"/></svg>
        + 12 555 0178 42
      </p>
      <p class="line">
        <svg viewBox="0 0 16 16" aria-hidden="true"><rect x="1.5" y="3.5" width="13" height="9" fill="none" stroke="var(--accent)" stroke-width="1.4"/><path d="M1.5 3.5 8 9l6.5-5.5" fill="none" stroke="var(--accent)" stroke-width="1.4"/></svg>
        daniel@brightmill.example
      </p>
      <p class="line">
        <svg viewBox="0 0 16 16" aria-hidden="true"><circle cx="8" cy="8" r="6.3" fill="none" stroke="var(--accent)" stroke-width="1.4"/><ellipse cx="8" cy="8" rx="2.7" ry="6.3" fill="none" stroke="var(--accent)" stroke-width="1.2"/><path d="M1.7 8h12.6" stroke="var(--accent)" stroke-width="1.2"/></svg>
        www.brightmilldata.example
      </p>
    </div>
  </section>

</body>
</html>
```